Real Estate Office Front Facade Redesign - ideas needed

Kindly read this brief thoroughly as there are 2 deliverables:
1. Office building façade redesign (see attached logo and also photo of our office building façade)
2. I also require a design for a freestanding signboard that will be coordinated with the design of the office front please see the images attached labelled signboard.

Deliverable number 1:
I am looking for a minimalist contemporary design with strong colours to draw the attention of the passing Traffic.

The office facade is to be repainted so you may choose to recolour the office in any way to coordinate with logo however the attached logo must remain as is. I prefer the colours red black and white or shades of these colours.

Velko property managers is a new company looking to target property investors in the local area. Most of our clients are from a middle to upper income demographic. We help these investors to rent out their properties and ensure they are maintained in good condition and provide a regular income.

The area we operate in is centrally located and close to the central business district of Perth.

Our office is situated in a residential area on a busy road facing diagonally at 45° down the road. People see our office from their cars whilst driving to work, there is no pedestrian traffic in the area. Therefore the office façade needs to stand out and any signage must be read by quickly passing traffic or convey our brand in seconds. Whilst the view of the office from the road is obscured somewhat by trees from a distance, once within 50 to 100 m of the office the full face of the office front is visible facing directly at the driver.

No measurements are provided for the façade of the office (please see the photo provided), this is a blank canvas as the whole building will be repainted to fit in with YOUR design. A logo is also attached. The colours red black and white are preferred.

Please provide an image of the office with signage/colours superimposed.

Deliverable number 2:
Also attached is an image of a freestanding sign for which I require a design. This sign is used for advertising properties for lease or sale which will be erected outside the front of residential houses. Again this sign needs to be bold and bright with a contemporary design. It needs to stand out from the crowd of many other signs in the area, whilst the sign advertises the property it must also promote our company brand by having a prominent logo. The size of these signboards will either be 1250 mm x 900 mm or 1800 mm x 625 mm. Please note that this sign must be rectangular in shape and cannot have any text or logo protruding outside of the lines of the rectangular sign due to cost restrictions.

Target Market(s)

Industry/Entity Type

Real Estate

Font styles to use
Sans Serif

Colors
ec1f27
ffffff
000000

Requirements
Must have
• Contemporary uncluttered design using the colours red black and white of shades of.
Nice to have
• A prominent logo with the words "Property Managers" easily read by passing traffic.
• Files provided with editable text and the name of the font used.
Should not have
• designs protruding outside of the overall building facia or sign rectangle.

```html
<!DOCTYPE html>
<html lang="en">
<head>
<meta charset="utf-8">
<title>Velko Property Managers – For Lease or Sale Signboard</title>
<link rel="stylesheet" href="https://fonts.googleapis.com/css2?family=Alegreya+Sans:wght@400;500&display=swap">
<style>
  :root {
    --brand-red: #ec1f27;
    --panel: #e8f5f5;
    --ink: #2f3a40;
    --white: #ffffff;
  }
  html, body {
    margin: 0;
    padding: 0;
    overflow: hidden;
    background: var(--white);
  }
  .signboard {
    position: relative;
    width: 1200px;
    height: 900px;
    background: var(--brand-red);
    font-family: "Alegreya Sans", sans-serif;
    overflow: hidden;
  }
  .panel {
    position: absolute;
    left: 21px;
    width: 1158px;
    background: var(--panel);
  }
  .panel--brand {
    top: 16px;
    height: 302px;
    border-radius: 20px 20px 0 0;
  }
  .panel--contact {
    top: 563px;
    height: 321px;
    border-radius: 0 0 20px 20px;
  }
  .brand-mark {
    position: absolute;
    left: 556px;
    top: 66px;
    width: 94px;
    height: 94px;
    background: var(--brand-red);
  }
  .brand-name {
    position: absolute;
    left: 0;
    right: 0;
    text-align: center;
    margin: 0;
    color: var(--ink);
    font-weight: 400;
  }
  .brand-name__main {
    top: 190px;
    font-size: 68px;
    line-height: 1;
    letter-spacing: 0.32em;
    padding-left: 0.32em;
  }
  .brand-name__sub {
    top: 266px;
    font-size: 19px;
    line-height: 1;
    letter-spacing: 0.3em;
    padding-left: 0.3em;
  }
  .headline {
    position: absolute;
    left: 0;
    right: 0;
    top: 356px;
    margin: 0;
    text-align: center;
    color: var(--white);
    font-weight: 500;
    font-size: 160px;
    line-height: 1;
    letter-spacing: 0.025em;
  }
  .contact {
    position: absolute;
    left: 0;
    right: 0;
    top: 618px;
    margin: 0;
    padding: 0;
    list-style: none;
    text-align: center;
    color: var(--ink);
    font-size: 62px;
    line-height: 70px;
    font-weight: 400;
  }
  .contact__web {
    font-size: 58px;
  }
</style>
</head>
<body>
  <main class="signboard">
    <section class="panel panel--brand" aria-label="Velko Property Managers"></section>
    <div class="brand-mark" aria-hidden="true"></div>
    <p class="brand-name brand-name__main">VELKO</p>
    <p class="brand-name brand-name__sub">PROPERTY MANAGERS</p>

    <h1 class="headline">For Lease or Sale</h1>

    <section class="panel panel--contact"></section>
    <ul class="contact">
      <li class="contact__mobile">Mobile 0400 1234 5678</li>
      <li class="contact__office">Office 9411 2233</li>
      <li class="contact__web">www.velko property.com.au</li>
    </ul>
  </main>
</body>
</html>
```